Kovát Lillas Physiotherapy Business Card Vienna

We need a business card design for a newly created Physiotherapy company based in Vienna Austria.
We seek a simple, modern, minimalist design without too much color variation. The font should look young/fresh, but definitely not childish or so. Since we are a starting Business, we currently haven't got a logo, if you feel like a logo would fit your design, feel free to use one, but it's not necessary.
Target Market(s)
Healthcare, young and elderly people with mobility issues
Industry/Entity Type
Health And Wellness
Contact Information for Business Card
Name: Lilla Kovát
Title description: Physiotherapist
Phone num: +43 664 2951 4086
e-mail: lilla.praxis@bluemail.example
Colors
Designer to choose colors to be used in the design.
Requirements
Must have
- Final design language must be in German, basically, the Title Description needs to be "Physiotherapeutin" the other details remain as in the English Language.
Nice to have
- Simple, modern, minimalist design
Should not have
- too many colors, Obvious use of a skeleton, skull, spline

```html
<!DOCTYPE html>
<html lang="de">
<head>
<meta charset="utf-8">
<title>Kovát Lillas Physiotherapy – Visitenkarte</title>
<link rel="stylesheet" href="https://fonts.googleapis.com/css2?family=Montserrat:wght@600&family=Questrial&display=swap">
<style>
  :root {
    --stage: #1a1a1a;
    --card: #232323;
    --card-edge: #2c2c2c;
    --ink: #ffffff;
    --ink-soft: #e6e6e6;
  }
  * { margin: 0; padding: 0; box-sizing: border-box; }
  html, body {
    width: 1200px; height: 900px; overflow: hidden;
    background: var(--stage);
  }
  .canvas {
    width: 1200px; height: 900px;
    display: flex; flex-direction: column; align-items: center; justify-content: center;
    gap: 36px;
  }
  .card {
    width: 700px; height: 400px;
    background: linear-gradient(135deg, var(--card) 0%, var(--card-edge) 100%);
    box-shadow: 0 14px 30px rgba(0,0,0,.55);
    color: var(--ink);
    position: relative;
  }
  .card-front { display: flex; align-items: center; justify-content: center; }
  .wordmark { display: flex; flex-direction: column; align-items: stretch; }
  .wordmark-name {
    font-family: "Montserrat", sans-serif; font-weight: 600;
    font-size: 40px; letter-spacing: 2px; line-height: 1;
  }
  .wordmark-trade {
    font-family: "Questrial", sans-serif;
    font-size: 19px; letter-spacing: 12.4px; line-height: 1; margin-top: 6px;
  }
  .card-back {
    display: flex; align-items: center; padding-left: 130px; gap: 24px;
  }
  .identity { text-align: right; }
  .identity-name {
    font-family: "Montserrat", sans-serif; font-weight: 600;
    font-size: 25px; letter-spacing: 2px; line-height: 1;
  }
  .identity-title {
    font-family: "Questrial", sans-serif;
    font-size: 18px; color: var(--ink-soft); margin-top: 4px;
  }
  .divider { width: 1px; height: 52px; background: var(--ink-soft); }
  .contact { list-style: none; font-family: "Questrial", sans-serif; font-size: 18px; color: var(--ink-soft); }
  .contact li { display: flex; align-items: center; gap: 10px; line-height: 1.5; white-space: nowrap; }
  .contact svg { width: 14px; height: 14px; flex: none; }
</style>
</head>
<body>
<main class="canvas">
  <section class="card card-front">
    <div class="wordmark">
      <span class="wordmark-name">KOVÁT LILLAS</span>
      <span class="wordmark-trade">PHYSIOTHERAPY</span>
    </div>
  </section>

  <section class="card card-back">
    <div class="identity">
      <p class="identity-name">LILLA KOVÁT</p>
      <p class="identity-title">Physiotherapeutin</p>
    </div>
    <span class="divider"></span>
    <ul class="contact">
      <li>
        <svg viewBox="0 0 24 24" aria-hidden="true"><path fill="none" stroke="#fff" stroke-width="2" d="M6 2l3 5-2 2c1 3 4 6 7 7l2-2 5 3-2 4C10 21 3 14 2 4z"/></svg>
        +43 664 2951 4086
      </li>
      <li>
        <svg viewBox="0 0 24 24" aria-hidden="true"><rect x="2" y="5" width="20" height="14" fill="none" stroke="#fff" stroke-width="2"/><path d="M2 5l10 8 10-8" fill="none" stroke="#fff" stroke-width="2"/></svg>
        lilla.praxis@bluemail.example
      </li>
    </ul>
  </section>
</main>
</body>
</html>
```